Brochure/flyer for our trip to Paris

Our company is taking us all on a summer trip to Paris. We have some key information that we need to tell everybody about the trip. We think a nicely designed brochure or flyer, which uses our brand colours and guidelines, would be something nice to keep during the trip and as a memento afterwards.

We are looking for a brochure or a flyer which contains all the info in the attached document.

This needs to happen really fast as we actually go to Paris on the 13th August. We also need time to print it!

We can provide a library of icons. All images in the document can be changed. you don't have to use the images in the document.

Target Market(s)

People in our company. They are fun and as this is for a party the flyer needs to feel uplifting.

Industry/Entity Type

Health

Font styles to use
Other font styles liked:
• Nexa - please see attached font.

Requirements
Must have
• Designers must stick to our brand guideline, font and the colours we use.
• Please also see attached content for the flyer.
• This website shows our style - https://www.lorventi.com/fr
Should not have
• Please don't make it too tacky or too much about French things. It can be a bit playful but not too much.

```html
<!DOCTYPE html>
<html lang="en">
<head>
<meta charset="utf-8">
<title>Paris Trip Brochure</title>
<link rel="stylesheet" href="https://fonts.googleapis.com/css2?family=Montserrat:wght@400;600;700&display=swap">
<style>
  :root{
    --bg:#e6e6e8;
    --page:#f5f4f6;
    --sky:#45a6dd;
    --sky-dark:#3a78c9;
    --teal:#00b3c8;
    --royal:#1f4f9f;
    --navy:#2d2a6e;
    --ink:#3d3d4a;
    --orange:#f05a28;
    --mist:#e9edf2;
    --white:#ffffff;
  }
  *{box-sizing:border-box;margin:0;padding:0}
  html,body{width:1200px;height:1000px;overflow:hidden}
  body{background:var(--bg);font-family:"Montserrat",sans-serif;color:var(--ink);position:relative}
  .spread{position:absolute;left:60px;top:120px;width:1080px;height:760px;display:flex;box-shadow:0 20px 40px rgba(0,0,0,.18)}
  .page{position:relative;width:540px;height:760px;background:var(--page);overflow:hidden}
  .page--right{background:var(--white)}
  .page--left::after{content:"";position:absolute;right:0;top:0;width:30px;height:100%;background:linear-gradient(to left,rgba(0,0,0,.08),transparent)}
  .abs{position:absolute}
  h2{font-weight:600;letter-spacing:.04em;text-transform:uppercase}
  p,li{font-size:11.5px;line-height:1.45}

  .travel{left:24px;top:0;width:440px;height:270px;background:var(--sky);color:var(--white);padding:36px 30px 0}
  .travel h2{font-size:17px;margin-bottom:14px}
  .travel h3{font-size:12.5px;font-weight:600;margin-top:4px}
  .travel p{font-size:11.5px;margin-bottom:12px}
  .travel-tab{left:24px;top:0}

  .art{background:linear-gradient(135deg,#f6a24a,#e9553a);border-radius:6px}
  .art--map{left:400px;top:230px;width:80px;height:72px;background:linear-gradient(135deg,#7cc46d,#4aa2d8 55%,#f07a3a)}
  .art--train{left:30px;top:300px;width:42px;height:42px;background:linear-gradient(#4f8fd8,#2f5fae)}
  .art--balloon{left:30px;top:40px;width:46px;height:60px;border-radius:50% 50% 40% 40%;background:linear-gradient(#f05a28,#e9e9ee)}
  .art--chat{left:430px;top:320px;width:80px;height:52px;border-radius:14px;background:rgba(255,255,255,.28)}
  .art--street{left:285px;top:440px;width:230px;height:180px;border-radius:0;background:linear-gradient(135deg,#e4e4e4,#cfcfd3)}

  .metro-title{left:84px;top:305px;color:var(--navy);font-size:16px;line-height:1.1}
  .metro-text{left:30px;top:358px;width:240px}
  .hotel{left:288px;top:345px;width:240px}
  .hotel h2{color:var(--navy);font-size:16px;margin-bottom:6px}
  .hotel p{color:var(--orange);font-size:11.5px;line-height:1.35}

  .tips-band{left:0;top:0}
  .tips{left:30px;top:660px;width:480px;color:var(--white)}
  .tips h4{font-weight:400;font-size:13px;margin-bottom:6px}
  .tips p{font-size:14px;line-height:1.35}

  .shapes-right{left:0;top:0}
  .phrases{left:40px;top:140px;width:470px;color:var(--white)}
  .phrases h2{font-size:15px;text-transform:none;letter-spacing:.02em;margin-bottom:10px}
  .phrases ol{list-style:none}
  .phrases li{font-size:11px;line-height:1.4}

  .itinerary{left:40px;top:462px;width:470px;color:var(--white)}
  .itinerary h2{font-size:15px;margin-bottom:6px}
  .itinerary p,.itinerary li{font-size:11px;line-height:1.42}
  .itinerary ul{list-style:none;margin-bottom:6px}

  .contacts{left:30px;top:690px;width:490px}
  .contacts h4{font-size:13px;font-weight:600;margin:0 0 4px 30px;color:var(--ink)}
  .contact-grid{display:grid;grid-template-columns:1fr 1fr;gap:2px 20px;padding-left:20px}
  .contact{font-size:13px;font-weight:600;color:var(--ink)}
  .contact span{color:var(--royal);margin-right:8px}
  .phone-icon{left:0;top:0}
</style>
</head>
<body>
<main class="spread">
  <section class="page page--left">
    <svg class="abs tips-band" width="540" height="760" aria-hidden="true">
      <polygon points="0,590 540,560 540,760 0,760" fill="var(--navy)"/>
    </svg>
    <div class="abs travel">
      <h2>Travel Information</h2>
      <h3>Outward Journey 13/08/16:</h3>
      <p>Meet at Kings Cross St Pancras International Station no later than 6:55am.<br>Our train departs at 7:55am and arrives in Paris at 11:17am local time.</p>
      <h3>Return Journey 14/08/16:</h3>
      <p>Meet at Gare Du Nord no later than 2pm.<br>Our train departs at 3:13pm and arrives in London at 4:30pm local time.</p>
    </div>
    <svg class="abs travel-tab" width="120" height="30" aria-hidden="true">
      <polygon points="0,0 120,0 100,22 0,22" fill="var(--sky-dark)"/>
    </svg>
    <div class="abs art art--map" role="img" aria-label="Folded city map with location pin"></div>
    <div class="abs art art--train" role="img" aria-label="Metro train icon"></div>
    <h2 class="abs metro-title">How to use<br>Metro</h2>
    <p class="abs metro-text">You have each been given 3 Metro tickets to help you on your way. Although you may need additional tickets depending on what your plans are in your free time. They are €4 for a single journey. Once you're in the Metro station, how to use the tickets is pretty self explanatory. Tip from Elodie: the tickets have a magnetic strip so try and keep them away from bank cards etc. If you find that any of your tickets do not work, you can ask at the kiosk for a replacement.</p>
    <div class="abs hotel">
      <h2>Hotel Information</h2>
      <p>HOTEL DES QUATRE VENTS<br>14, rue des Tilleuls<br>75001 Paris France<br>Tel: +33 1 45 18 27 60</p>
    </div>
    <div class="abs art art--street" role="img" aria-label="Street map around the hotel"></div>
    <div class="abs tips">
      <h4>Top Tips:</h4>
      <p>The best way to find your way around is to use RouteWise or alternatively:<br>http://www.metroguide-paris.fr/itineraires/en/recherche</p>
    </div>
  </section>

  <section class="page page--right">
    <svg class="abs shapes-right" width="540" height="760" aria-hidden="true">
      <polygon points="0,120 540,80 540,410 0,450" fill="var(--teal)"/>
      <path d="M0,450 L540,410 L540,700 C380,680 180,670 0,685 Z" fill="var(--royal)"/>
      <path d="M0,685 C180,670 380,680 540,700 L540,760 L0,760 Z" fill="var(--mist)"/>
    </svg>
    <div class="abs art art--balloon" role="img" aria-label="Hot air balloon illustration"></div>
    <div class="abs art art--chat" role="img" aria-label="Speech bubbles"></div>
    <div class="abs phrases">
      <h2>Some Must-know French Phrases for Savvy Travellers:</h2>
      <ol>
        <li>1. Bonjour. (Hello)</li>
        <li>2. Oui / Non (Yes / No)</li>
        <li>3. Parlez-vous anglais ? (Do you speak English?)</li>
        <li>4. Où est le métro? (Where is the Metro?)</li>
        <li>5. Où est… ? (Where is…?)</li>
        <li>6. Où est le guichet ? (Where is the ticket window?)</li>
        <li>7. Combien ça coûte? (How much does it cost?)</li>
        <li>8. Merci! (Thank you!)</li>
        <li>9. Bonsoir (Hello/good evening)</li>
        <li>10. Au Revoir (Goodbye)</li>
        <li>11. Puis-je me connecter à Internet? (Can I get on the internet?)</li>
        <li>12. Je ne comprends pas. (I don't understand)</li>
        <li>13. Je ne sais pas. (I don't know)</li>
        <li>14. Est-ce que vous pouvez l'écrire? (Could you please write it down?)</li>
        <li>15. Pouvez-vous m'aider, s'il vous plaît? (Can you help me please?)</li>
      </ol>
    </div>
    <div class="abs itinerary">
      <h2>Itinerary</h2>
      <p>13TH AUGUST</p>
      <p>Arrive in Paris at 11:17am local time.</p>
      <ul>
        <li>- Drop bags to hotel, grab lunch and enjoy our 1 hour River Seine Tour.</li>
        <li>- Free time 2:30–7pm (you will need to go and officially check in at the hotel and get ready for the evening within this time)</li>
        <li>- 7pm: Drinks and dinner at…………</li>
        <li>- Late night drinks at…………</li>
      </ul>
      <p>The next day…..</p>
      <ul>
        <li>- Check out between 9–10am at the latest and enjoy some breakfast at the hotel.</li>
        <li>- Casual walk up to Gare du Nord, enjoying Paris that little bit more before we leave.</li>
        <li>- Everyone must be at Gare du Nord by 2pm at the very latest to check in!</li>
      </ul>
    </div>
    <div class="abs contacts">
      <svg class="abs phone-icon" width="22" height="22" viewBox="0 0 24 24" aria-hidden="true">
        <path fill="var(--royal)" d="M6.6 10.8a15.1 15.1 0 0 0 6.6 6.6l2.2-2.2a1 1 0 0 1 1-.25 11.4 11.4 0 0 0 3.6.57 1 1 0 0 1 1 1V20a1 1 0 0 1-1 1A17 17 0 0 1 3 4a1 1 0 0 1 1-1h3.5a1 1 0 0 1 1 1c0 1.25.2 2.450.57 3.570a1 1 0 0 1-.25 1z"/>
      </svg>
      <h4>Emergency Internal Contacts:</h4>
      <div class="contact-grid">
        <p class="contact"><span>Maren</span>07700900412</p>
        <p class="contact"><span>Owen</span>07700900236</p>
        <p class="contact"><span>Tobias</span>07700900587</p>
        <p class="contact"><span>Leyla</span>07700900849</p>
      </div>
    </div>
  </section>
</main>
</body>
</html>
```